Business Card for Professional Photographer

I'm looking for an eye catching modern clean design that compliments my logo/ website fonts & colours.
I specialise in architecture, corporate & commercial photography so I'm marketing to professional clients rather than portrait / wedding clients.

I would prefer to not have a solid black design.

My logo brand guide is as follows :

Main front font. : Reislust
Main font colour : #fff
Slogan front font : Ubuntu Bold
Monogram front font : Venti Medium
Container colour : #fff

I need print ready files in pdf .png & .eps formats.

Included in the files below are some screen grabs as reference to font & colours etc.

```html
<!DOCTYPE html>
<html lang="en">
<head>
<meta charset="utf-8">
<title>Angle &amp; Light — Business Card</title>
<link href="https://fonts.googleapis.com/css2?family=Ubuntu:wght@300;400;500;700&display=swap" rel="stylesheet">
<style>
  :root {
    --backdrop: #e6e6e4;
    --gold: #c9934f;
    --gold-light: #f8eaa8;
    --gold-mid: #dcae62;
    --ink: #4a4a4a;
    --ink-soft: #66625c;
    --paper: #ffffff;
  }
  * { box-sizing: border-box; margin: 0; padding: 0; }
  html, body {
    width: 1200px; height: 960px; overflow: hidden;
    background: var(--backdrop);
    font-family: "Ubuntu", sans-serif;
  }
  .canvas { position: relative; width: 1200px; height: 960px; }

  .card {
    position: absolute;
    width: 700px; height: 400px;
    border-radius: 22px;
    box-shadow: 0 14px 30px rgba(0,0,0,.18);
    overflow: hidden;
  }

  /* Front — gold */
  .card-front {
    left: 110px; top: 60px;
    background: radial-gradient(ellipse 60% 65% at 52% 42%, var(--gold-light) 0%, var(--gold-mid) 55%, var(--gold) 100%);
    color: var(--ink-soft);
  }
  .brand {
    position: absolute; left: 0; right: 0; top: 150px;
    display: flex; justify-content: center; align-items: center; gap: 16px;
  }
  .brand-mark {
    width: 26px; height: 26px; background: var(--ink-soft);
  }
  .brand-text { display: flex; flex-direction: column; }
  .brand-name {
    font-weight: 400; font-size: 32px; letter-spacing: 1px;
  }
  .brand-tagline {
    font-weight: 400; font-size: 12px; letter-spacing: 1px; margin-top: 4px;
  }
  .front-web {
    position: absolute; left: 0; right: 0; bottom: 90px;
    text-align: center; font-size: 15px; letter-spacing: 4px;
  }

  /* Back — white with gold frame */
  .card-back {
    left: 390px; top: 500px;
    background: var(--paper);
  }
  .frame {
    position: absolute; inset: 14px;
    border: 8px solid var(--gold);
  }
  .details {
    position: absolute; inset: 0;
    display: flex; justify-content: center; align-items: center; gap: 22px;
  }
  .identity { text-align: right; color: var(--ink); }
  .person-name { color: var(--gold); font-weight: 500; font-size: 28px; }
  .person-role { font-weight: 700; font-size: 15px; margin-top: 2px; }
  .address { font-size: 16px; line-height: 1.35; margin-top: 22px; }
  .divider { width: 1.5px; height: 118px; background: var(--ink-soft); opacity: .7; }
  .contacts { list-style: none; color: var(--ink); font-size: 15px; line-height: 1.45; }
  .contacts li { display: flex; align-items: center; gap: 8px; }
  .contacts svg { width: 13px; height: 13px; fill: var(--gold); flex: none; }
</style>
</head>
<body>
<main class="canvas">
  <section class="card card-front">
    <div class="brand">
      <div class="brand-mark"></div>
      <div class="brand-text">
        <span class="brand-name">Angle &amp; Light</span>
        <span class="brand-tagline">Spaces · People · Products</span>
      </div>
    </div>
    <p class="front-web">www.angleandlight.com</p>
  </section>

  <section class="card card-back">
    <div class="frame"></div>
    <div class="details">
      <div class="identity">
        <p class="person-name">Daniel Hart</p>
        <p class="person-role">President</p>
        <p class="address">2140 Cedar Ridge Road<br>Juneau, Alaska 99801</p>
      </div>
      <div class="divider"></div>
      <ul class="contacts">
        <li><svg viewBox="0 0 16 16"><path d="M3 1l3 3-1.5 2a9 9 0 0 0 5.5 5.5L12 10l3 3-2 2C7 15 1 9 1 3z"/></svg>555-214-7730</li>
        <li><svg viewBox="0 0 16 16"><path d="M4 0h8v16H4zM5.5 2v10h5V2z"/></svg>555-618-2049</li>
        <li><svg viewBox="0 0 16 16"><path d="M4 1h8v4H4zM1 6h14v7H1zM4 11h8v4H4z"/></svg>555-390-4416</li>
        <li><svg viewBox="0 0 16 16"><path d="M1 3h14v1L8 9 1 4zM1 6l7 5 7-5v7H1z"/></svg>info@angleandlight.com</li>
        <li><svg viewBox="0 0 16 16"><circle cx="8" cy="8" r="7"/></svg>www.angleandlight.com</li>
      </ul>
    </div>
  </section>
</main>
</body>
</html>
```